Automotive Accessories Business Card

Design a business template that match our new logo design and our industry.

https://www.qelmotorgear.com/

Target Market(s)

Aftermarket auto parts and accessories

Industry/Entity Type

automotive

Contact Information for Business Card

company logo

Font styles to use
Serif
Sans Serif

Colors
EB3D1F
EC4F4E
F09395
F8D3D4
FCEDEE

```html
<!DOCTYPE html>
<html lang="en">
<head>
<meta charset="utf-8">
<title>QEL Motor Gear — Business Card</title>
<link href="https://fonts.googleapis.com/css2?family=Arimo:wght@400;700&display=swap" rel="stylesheet">
<style>
  :root {
    --brand-red: #d9202a;
    --ink: #1f1f1f;
    --paper: #ffffff;
    --stage: #c9c9c9;
    --band-grey: #e6e6e6;
    --pattern-grey: #dcdcdc;
  }
  * { box-sizing: border-box; margin: 0; padding: 0; }
  html, body { width: 1200px; height: 900px; overflow: hidden; }
  body {
    background: var(--stage);
    font-family: "Arimo", Arial, sans-serif;
    position: relative;
  }
  .card {
    position: absolute;
    width: 640px;
    height: 366px;
    border-radius: 28px;
    overflow: hidden;
    box-shadow: 0 8px 22px rgba(0,0,0,.25);
  }
  .card__decor { position: absolute; inset: 0; width: 100%; height: 100%; }

  /* Front */
  .card--front { left: 60px; top: 60px; background: var(--brand-red); }
  .wordmark {
    position: absolute;
    display: flex;
    align-items: center;
    gap: 14px;
    font-weight: 700;
    letter-spacing: 1px;
    white-space: nowrap;
  }
  .wordmark__square { display: block; }
  .card--front .wordmark {
    left: 0; right: 0; top: 152px;
    justify-content: center;
    color: var(--paper);
    font-size: 46px;
  }
  .card--front .wordmark__square { width: 30px; height: 30px; background: var(--paper); }

  /* Back */
  .card--back { left: 500px; top: 474px; background: var(--paper); }
  .card--back .wordmark {
    left: 48px; top: 62px;
    color: var(--brand-red);
    font-size: 38px;
  }
  .card--back .wordmark__square { width: 24px; height: 24px; background: var(--brand-red); }
  .person { position: absolute; left: 48px; top: 168px; }
  .person__name { color: var(--brand-red); font-weight: 700; font-size: 28px; letter-spacing: .5px; }
  .person__title { color: var(--ink); font-size: 17px; margin-top: 2px; }
  .contacts { position: absolute; left: 48px; top: 250px; list-style: none; }
  .contacts li {
    display: flex; align-items: center; gap: 10px;
    color: var(--ink); font-size: 16px; line-height: 26px;
  }
  .contacts svg { width: 16px; height: 16px; flex: none; }
  .contacts .accent { color: var(--brand-red); }
  .address {
    position: absolute; right: 40px; top: 196px;
    text-align: right; color: var(--ink); font-size: 15px; line-height: 21px;
    font-style: normal;
  }
</style>
</head>
<body>

<section class="card card--front" aria-label="Business card front">
  <svg class="card__decor" viewBox="0 0 640 366" preserveAspectRatio="none" aria-hidden="true">
    <polygon points="500,0 640,0 640,366 380,366" fill="#ffffff" fill-opacity=".10"/>
  </svg>
  <svg class="card__decor" viewBox="0 0 640 366" preserveAspectRatio="none" role="img" aria-label="Chequered flag pattern">
    <rect x="400" y="250" width="240" height="116" fill="#ffffff" fill-opacity=".08"/>
  </svg>
  <div class="wordmark"><span class="wordmark__square"></span>QEL MOTOR GEAR</div>
</section>

<section class="card card--back" aria-label="Business card back">
  <svg class="card__decor" viewBox="0 0 640 366" preserveAspectRatio="none" aria-hidden="true">
    <polygon points="470,0 560,0 440,366 350,366" fill="var(--band-grey)" fill-opacity=".7"/>
    <polygon points="585,0 640,0 640,366 500,366" fill="var(--band-grey)" fill-opacity=".7"/>
  </svg>
  <svg class="card__decor" viewBox="0 0 640 366" preserveAspectRatio="none" role="img" aria-label="Chequered flag pattern">
    <rect x="380" y="262" width="260" height="104" fill="var(--pattern-grey)" fill-opacity=".6"/>
  </svg>

  <div class="wordmark"><span class="wordmark__square"></span>QEL MOTOR GEAR</div>

  <div class="person">
    <p class="person__name">MARCUS DELANE</p>
    <p class="person__title">Managing Director</p>
  </div>

  <ul class="contacts">
    <li>
      <svg viewBox="0 0 16 16" aria-hidden="true"><path d="M4 1.5l2.2 3-1.3 1.4a8 8 0 0 0 5.2 5.2l1.4-1.3 3 2.2-1.4 2.4C7.6 14.6 1.4 8.4 1.6 2.9z" fill="var(--brand-red)"/></svg>
      044-555 210 347
    </li>
    <li>
      <svg viewBox="0 0 16 16" aria-hidden="true"><rect x="1" y="3" width="14" height="10" fill="var(--brand-red)"/><path d="M1.5 3.5L8 9l6.5-5.5" stroke="#fff" stroke-width="1.3" fill="none"/></svg>
      info@qelmotorgear.com
    </li>
    <li>
      <svg viewBox="0 0 16 16" aria-hidden="true"><g fill="none" stroke="var(--brand-red)" stroke-width="1.4"><circle cx="8" cy="8" r="6.5"/><ellipse cx="8" cy="8" rx="3" ry="6.5"/><path d="M1.5 8h13"/></g></svg>
      <span>www.<span class="accent">qelmotorgear</span>.com</span>
    </li>
  </ul>

  <address class="address">
    18 Harbor Works Road<br>
    37819, Northvale
  </address>
</section>

</body>
</html>
```